Stationary design for boutique production house

We need a stationary design for our production house, 'Lorno Productions' based in Singapore. We produce microfilms as well as podcasts, talkshows and events. Our logo is a stylized icon of our director, who is also the executive producer and host of our programs, Lorno. Our main company colors are Red, Black and white. We would like a clean, minimalist design incorporating our existing company logo that conveys a sense of urbanism and elegance.

Logo and font files are attached. f

Target Market(s)

We focus on lifestyle media rather than entertainment.

Industry/Entity Type

Boutique

Font styles to use
Serif
Sans Serif

Colors
ec1f27
ffffff
000000

Requirements
Must have
• Our company logo and at least one of our company colors.
Nice to have
• Our address and contact information.
Should not have
• Changes made to the company logo (using only certain parts of it is fine though)

```html
<!DOCTYPE html>
<html lang="en">
<head>
<meta charset="utf-8">
<title>Lorno Productions – Business Card</title>
<link rel="stylesheet" href="https://fonts.googleapis.com/css2?family=Questrial&family=Playfair+Display:wght@400;700&display=swap">
<style>
  :root {
    --stage: #3a3a3a;
    --card-dark: #231f20;
    --card-darker: #1b1819;
    --pattern-tone: #2e2a2b;
    --paper: #ffffff;
    --ink: #000000;
    --red: #ec1f27;
    --text-light: #f2f2f2;
    --sans: "Questrial", "Helvetica Neue", Arial, sans-serif;
    --serif: "Playfair Display", Georgia, serif;
  }
  * { box-sizing: border-box; margin: 0; padding: 0; }
  html, body { width: 1200px; height: 768px; overflow: hidden; }
  body {
    background: var(--stage);
    font-family: var(--sans);
    position: relative;
  }
  .card {
    position: absolute;
    top: 224px;
    width: 560px;
    height: 320px;
    overflow: hidden;
  }
  .card--back { left: 20px; background: var(--card-dark); }
  .card--front { left: 620px; display: flex; }

  /* back */
  .back-pattern {
    position: absolute; inset: 0;
    background: radial-gradient(circle at 30% 40%, var(--pattern-tone), var(--card-darker) 75%);
  }
  .back-mark {
    position: absolute; right: 40px; bottom: 44px;
    display: flex; align-items: center; gap: 10px;
    color: var(--paper);
    font-family: var(--sans);
    font-size: 30px;
    letter-spacing: 3px;
    text-transform: uppercase;
  }
  .mark-dot { width: 12px; height: 12px; border-radius: 50%; background: var(--red); flex: none; }
  .back-web {
    position: absolute; right: 40px; bottom: 20px;
    font-family: var(--serif); font-size: 13px; color: var(--text-light);
    letter-spacing: .5px;
  }

  /* front */
  .front-info {
    width: 268px; height: 100%;
    background: var(--card-dark);
    color: var(--text-light);
    padding: 34px 22px 0 30px;
    font-size: 14.5px;
    line-height: 1.3;
  }
  .person-name { color: var(--red); font-size: 17px; letter-spacing: 1px; text-transform: uppercase; }
  .person-role { text-transform: uppercase; }
  .rule { border: 0; border-top: 2px dotted var(--red); margin: 12px 0 14px; }
  .contact-list { list-style: none; }
  .contact-list li { display: flex; align-items: center; gap: 8px; }
  .contact-list svg { width: 13px; height: 13px; fill: var(--red); flex: none; }

  .front-brand {
    flex: 1; background: var(--paper);
    display: flex; align-items: center; justify-content: center;
    padding: 0 36px;
  }
  .brand-mark {
    display: flex; align-items: center; gap: 12px;
    color: var(--ink);
    font-family: var(--sans);
    font-size: 20px;
    line-height: 1.25;
    letter-spacing: 2px;
    text-transform: uppercase;
    text-align: center;
  }
  .brand-name { display: flex; flex-direction: column; }
</style>
</head>
<body>

<section class="card card--back" aria-label="Card back">
  <div class="back-pattern" role="img" aria-label="Repeating tone-on-tone pattern of the company symbol"></div>
  <div class="back-mark"><span class="mark-dot"></span>Lorno</div>
  <p class="back-web">www.lornoproductions.sg</p>
</section>

<section class="card card--front" aria-label="Card front">
  <div class="front-info">
    <p class="person-name">Marcus Vale</p>
    <p class="person-role">CEO/Founder</p>
    <p>marcus@lornoproductions.sg</p>
    <hr class="rule">
    <p>42 Amber Quay</p>
    <p>Singapore 048921</p>
    <p>www.lornoproductions.sg</p>
    <hr class="rule">
    <ul class="contact-list">
      <li><svg viewBox="0 0 16 16" aria-hidden="true"><path d="M3.5 1l2.5 3-1.5 2c1 2 3 4 5 5l2-1.5 3 2.5-1.5 2.5C8 15 1 8 1 2.5z"/></svg>612 408 3357</li>
      <li><svg viewBox="0 0 16 16" aria-hidden="true"><path d="M4 0h8v16H4zM5.5 2v10h5V2z"/></svg>817 592 4013</li>
      <li><svg viewBox="0 0 16 16" aria-hidden="true"><path d="M4 1h8v4H4zM1 6h14v7h-3v2H4v-2H1zM5 10v4h6v-4z"/></svg>463 215 8870</li>
    </ul>
  </div>
  <div class="front-brand">
    <div class="brand-mark">
      <span class="mark-dot"></span>
      <span class="brand-name"><span>Lorno</span><span>Productions</span></span>
    </div>
  </div>
</section>

</body>
</html>
```